Lantern Petals Website v.1 - attract floral shop franchisees

I need a simple information website for my new business. We are a franchisor of flower shops. The overall purpose of the website is to promote the company and the service, especially to potential franchisees and retailers. Only about 4 pages are required including homepage, About, For Supermarkets, For Franchisees, and Contact. No special functions are required except the site will have two separate inquiry forms that must be filled out online and submitted via automated email. Similarly, an email form should be linked from the Contact page. I have a logo and business cards designed by ArtMingle, and I would like the site to have a consistent color scheme and style. The key to design will be to express the joy and love associated with flowers and floral bouquets.
IMPORTANT - I will be exporting the website design to Wordpress CMS in a site hosted by HostNimbus. For smooth integration into WordPress hosted by HostNimbus, the designer should build the site using a WordPress-friendly format. Ideally, they should use HTML, CSS, and PHP. Creating a custom theme or using a page builder that exports to WordPress-compatible files is best. This ensures the site can be easily imported and managed within WordPress.

Target Market(s)

Potential franchisees (existing florists or creative types who might like to own a floral business) and supermarkets who might want us to run their floral department

Industry/Entity Type

Floral retailing

Requirements
Must have
• A brand theme that is beautiful, consistent throughout and builds on the logo design
Nice to have
• Show gender and ethnic diversity in customers and florists. Pictures of happy florists (for franchisees) and pictures of amazing floral department displays (for supermarkets)

```html
<!DOCTYPE html>
<html lang="en">
<head>
<meta charset="utf-8">
<title>Lantern Petals – Flower Shop Franchises</title>
<link href="https://fonts.googleapis.com/css2?family=Poppins:wght@400;500;600;700&family=Oswald:wght@600&family=Great+Vibes&display=swap" rel="stylesheet">
<style>
:root{
  --green:#2f8a2c;
  --green-dark:#1f5e1d;
  --green-soft:#e6f1dc;
  --orange:#f4a316;
  --ink:#222;
  --muted:#555;
  --line:#dcdcdc;
  --footer:#0d0d0d;
}
*{box-sizing:border-box;margin:0;padding:0}
html,body{width:1200px;height:4520px;overflow:hidden}
body{font-family:'Poppins',sans-serif;color:var(--ink);background:#fff;position:relative}
.section{position:absolute;left:0;width:1200px;overflow:hidden}
.script{font-family:'Great Vibes',cursive;font-weight:400;color:var(--green-dark)}
.btn{display:inline-flex;align-items:center;gap:10px;background:var(--orange);color:#fff;font-size:14px;font-weight:500;padding:9px 10px 9px 22px;border-radius:22px}
.btn .dot{width:24px;height:24px;border-radius:50%;background:#fff}
.photo{border-radius:6px}
.heading{display:flex;align-items:flex-end;gap:10px;font-size:36px;font-weight:700;white-space:nowrap}
.heading .leaf{width:16px;height:16px;border-radius:50%;background:var(--green);align-self:center;flex:none}
.heading .script{font-size:52px;line-height:1}

/* header */
.site-header{top:0;height:64px;background:#fff}
.brand{position:absolute;left:140px;top:10px;display:flex;align-items:center;gap:10px}
.brand .mark{width:34px;height:34px;border-radius:50%;background:var(--orange)}
.brand span{font-size:20px;font-weight:600;color:var(--green)}
.topline{position:absolute;right:40px;top:8px;display:flex;gap:24px;font-size:13px;color:var(--muted)}
.topline i{display:inline-block;width:10px;height:10px;border-radius:50%;background:var(--green);margin-right:6px}
.nav{position:absolute;left:490px;top:36px;display:flex;gap:34px;font-size:14px}
.nav .active{color:var(--orange);border-bottom:2px solid var(--orange);padding-bottom:4px}

/* hero */
.hero{top:64px;height:576px}
.hero-bg{position:absolute;inset:0;background:linear-gradient(100deg,#6d7a5c 0%,#a7a68e 40%,#e6ddd4 65%,#f1e7e3 100%)}
.hero-text{position:absolute;left:140px;top:170px;font-family:'Oswald',sans-serif;font-size:58px;line-height:1.12;color:#fff;font-weight:600}
.hero .btn{position:absolute;left:140px;top:440px;padding:12px 26px}

/* about */
.about{top:640px;height:600px;background:linear-gradient(180deg,#eef6e6,#fff 60%)}
.about .frame{position:absolute;left:180px;top:120px;width:260px;height:270px;background:linear-gradient(160deg,#c9b6a4,#6f7a63);border:6px solid #fff;box-shadow:0 4px 14px rgba(0,0,0,.15)}
.about .flowers{position:absolute;left:0;top:300px;width:260px;height:220px;border-radius:0 60% 60% 0;background:radial-gradient(circle at 40% 50%,#f2a07c,#f7d3bf 60%,transparent 75%)}
.about .badge{position:absolute;left:395px;top:345px;width:90px;height:90px;border-radius:50%;background:#fff;border:4px solid #eee}
.about .heading{position:absolute;left:600px;top:100px}
.about-copy{position:absolute;left:600px;top:190px;width:430px;font-size:12.5px;line-height:1.6;color:var(--muted)}
.about-copy p+p{margin-top:12px}
.about .btn{position:absolute;left:600px;top:480px}

/* opportunity */
.opportunity{top:1240px;height:720px;background:linear-gradient(180deg,#fff,#f7f2ee)}
.opportunity .heading{position:absolute;left:300px;top:70px}
.cards{position:absolute;left:150px;top:210px;display:flex;gap:30px}
.card{width:280px;height:340px;border-radius:22px;border:6px solid #fff;box-shadow:0 6px 18px rgba(0,0,0,.15);position:relative;overflow:hidden}
.card:nth-child(1){background:linear-gradient(170deg,#8a9a6a,#3e5a36)}
.card:nth-child(2){background:linear-gradient(170deg,#c9a98a,#6c5a48)}
.card:nth-child(3){background:linear-gradient(170deg,#b9c79a,#5f7547)}
.card span{position:absolute;left:0;right:0;top:140px;text-align:center;color:#fff;font-size:22px;font-weight:600;line-height:1.3;text-shadow:0 2px 6px rgba(0,0,0,.4)}
.opportunity .btn{position:absolute;left:520px;top:600px}
.opportunity .bouquet{position:absolute;right:0;top:470px;width:170px;height:220px;background:radial-gradient(circle,#e36b8a,#f3b7c5 55%,transparent 72%)}

/* why */
.why{top:1960px;height:720px;background:linear-gradient(180deg,#eef6e6,#fff)}
.why .heading{position:absolute;left:100px;top:110px;font-size:32px}
.why .heading .script{font-size:46px}
.why ul{position:absolute;left:110px;top:210px;list-style:none;font-size:13.5px;line-height:1.55}
.why li{display:flex;align-items:center;gap:10px;margin-bottom:4px}
.why li::before{content:"";width:12px;height:12px;border-radius:50%;background:var(--green);flex:none}
.why .frame{position:absolute;left:680px;top:70px;width:440px;height:560px;background:linear-gradient(160deg,#d8c3b8,#9a6f6c 55%,#6d4a52);border:8px solid #fff;box-shadow:0 6px 20px rgba(0,0,0,.15)}

/* growth */
.growth{top:2680px;height:620px;background:#fff}
.growth .heading{position:absolute;left:470px;top:40px}
.growth p{position:absolute;left:280px;top:130px;width:640px;text-align:center;font-size:12.5px;line-height:1.6;color:var(--muted)}
.growth .map{position:absolute;left:220px;top:220px;width:760px;height:360px;border-radius:50%;background:radial-gradient(ellipse,#ececec,#fff 70%)}
.growth svg{position:absolute;left:380px;top:250px}
.growth .bloom{position:absolute;left:0;top:380px;width:230px;height:240px;background:radial-gradient(circle,#f19a82,#f8d4c8 55%,transparent 72%)}

/* faq */
.faq{top:3300px;height:660px;background:linear-gradient(180deg,#fff,#eef6e6)}
.faq .heading{position:absolute;left:310px;top:30px}
.faq-list{position:absolute;left:280px;top:140px;width:640px}
.faq-item{background:#fff;border:1px solid var(--line);margin-bottom:14px;padding:16px 20px;font-size:13.5px;font-weight:500;display:flex;justify-content:space-between;box-shadow:0 2px 6px rgba(0,0,0,.05)}
.faq-item.open{display:block;border-bottom:3px solid var(--green)}
.faq-item.open p{font-size:12px;font-weight:400;color:var(--muted);line-height:1.6;margin-top:12px}
.faq-item b{font-weight:600;color:var(--green)}
.faq .bouquet{position:absolute;right:20px;top:200px;width:230px;height:320px;background:radial-gradient(circle,#b27ad0,#efc6d6 55%,transparent 72%)}

/* contact */
.contact{top:3960px;height:440px;background:#fff}
.contact .ghost{position:absolute;left:0;right:0;top:20px;text-align:center;font-size:180px;font-weight:700;letter-spacing:8px;color:#f4f4f4;line-height:1}
.contact-form{position:absolute;left:210px;top:180px;width:440px}
.contact h2,.details h2{font-size:28px;font-weight:600;margin-bottom:18px}
.contact-form h2{text-align:center}
.row{display:flex;gap:18px;margin-bottom:14px}
.field{flex:1;height:40px;border:1px solid var(--line);font-size:12px;color:#999;padding:12px;background:#fff}
.field.tall{height:80px}
.contact-form .btn{margin:6px auto 0;display:flex;width:150px}
.details{position:absolute;left:670px;top:150px;width:320px;height:250px;background:var(--green-soft);border-radius:8px;padding:26px 28px}
.details .item{display:flex;gap:12px;font-size:12.5px;margin-bottom:14px;align-items:flex-start;color:var(--muted)}
.details .ico{width:28px;height:28px;border-radius:50%;background:var(--orange);flex:none}
.social{display:flex;gap:16px;font-size:12px;color:var(--muted)}
.social i{display:inline-block;width:12px;height:12px;border-radius:50%;background:var(--green);margin-right:5px;vertical-align:middle}

/* footer */
.site-footer{top:4400px;height:120px;background:var(--footer);color:#ddd}
.site-footer .brand{left:180px;top:28px}
.site-footer .brand span{color:var(--orange)}
.flinks{position:absolute;left:500px;top:40px;display:flex;gap:38px;font-size:13px}
.copy{position:absolute;left:0;right:0;top:92px;text-align:center;font-size:11px;color:#999}
</style>
</head>
<body>

<header class="section site-header">
  <div class="brand"><div class="mark"></div><span>Lantern Petals</span></div>
  <div class="topline"><span><i></i>123-456-7890</span><span><i></i>info@lanternpetals.com</span></div>
  <nav class="nav"><span class="active">Home</span><span>About Us</span><span>For Supermarkets</span><span>For Franchisees</span></nav>
</header>

<section class="section hero">
  <div class="hero-bg" role="img" aria-label="Smiling florist arranging fresh roses in a flower shop"></div>
  <h1 class="hero-text">Freshest Flowers<br>Artisan Designs<br>Franchise Opportunities</h1>
  <span class="btn">Contact Us</span>
</section>

<section class="section about">
  <div class="flowers" role="img" aria-label="Orange and peach roses"></div>
  <div class="frame photo" role="img" aria-label="Florist standing among bouquets in a shop"></div>
  <div class="badge"></div>
  <h2 class="heading"><span class="leaf"></span>About <span class="script">Lantern</span></h2>
  <div class="about-copy">
    <p>Fresh flowers convey beauty and love, and in our view everyone should enjoy them every day. Lantern Petals is a franchise brand created to make top quality fresh flowers and professionally designed bouquets accessible to every consumer at affordable prices.</p>
    <p>Professional florists typically sell the finest quality stems, design the most beautiful bouquets and provide the finest customer service, but their costs and floral products remain high. Supermarket flower departments benefit from high customer footfall, economies of scale and low pricing, but their quality and design are often limited. We bring the best of both together in one trusted model.</p>
  </div>
  <span class="btn">Get Started <span class="dot"></span></span>
</section>

<section class="section opportunity">
  <h2 class="heading"><span class="leaf"></span>Opportunity For <span class="script">Franchisees</span></h2>
  <div class="cards">
    <div class="card" role="img" aria-label="Supermarket floral display"><span>Supermarkets</span></div>
    <div class="card" role="img" aria-label="New franchisee arranging flowers"><span>New Floral<br>Franchisees</span></div>
    <div class="card" role="img" aria-label="Professional florist in her shop"><span>Professional Florist<br>Retailers</span></div>
  </div>
  <span class="btn">Get Started <span class="dot"></span></span>
  <div class="bouquet" role="img" aria-label="Pink flower bouquet"></div>
</section>

<section class="section why">
  <h2 class="heading"><span class="leaf"></span>Why Partner With <span class="script">Lantern</span></h2>
  <ul>
    <li>Low investment and high returns</li>
    <li>Ready made business in local locality</li>
    <li>ROI in 12-15 months</li>
    <li>Delivery throughout the city in less than 2 hours</li>
    <li>Help in selecting the right location</li>
    <li>Trained manpower support (florist)</li>
    <li>Training for franchisee and team</li>
    <li>Exclusive merchandise and design support</li>
    <li>Visual merchandising support</li>
    <li>Quality control team for upkeep of store</li>
  </ul>
  <div class="frame photo" role="img" aria-label="Florist smelling a large colourful bouquet"></div>
</section>

<section class="section growth">
  <h2 class="heading"><span class="leaf"></span>Our <span class="script">Growth</span></h2>
  <p>Our network has grown steadily since launch, with new stores opening in every region each year. Franchise partners benefit from shared buying power, proven systems and a brand customers already trust, helping each store reach healthy profit sooner.</p>
  <div class="map" role="img" aria-label="Faint world map"></div>
  <svg width="440" height="300" viewBox="0 0 440 300">
    <g fill="#2f9e35">
      <rect x="40" y="220" width="34" height="60"/>
      <rect x="90" y="195" width="34" height="85"/>
      <rect x="140" y="165" width="34" height="115"/>
      <rect x="190" y="135" width="34" height="145"/>
      <rect x="240" y="105" width="34" height="175"/>
      <rect x="290" y="75" width="34" height="205"/>
      <rect x="340" y="45" width="34" height="235"/>
    </g>
    <line x1="20" y1="282" x2="400" y2="282" stroke="#999" stroke-width="2"/>
    <path d="M20 200 L180 120 L240 110 L370 30" fill="none" stroke="#e8451e" stroke-width="10" stroke-linecap="round"/>
    <polygon points="345,20 395,15 380,60" fill="#e8451e"/>
  </svg>
  <div class="bloom" role="img" aria-label="Peach carnations"></div>
</section>

<section class="section faq">
  <h2 class="heading"><span class="leaf"></span>Frequently Asked <span class="script">Questions</span></h2>
  <div class="faq-list">
    <div class="faq-item open"><div style="display:flex;justify-content:space-between">What does it cost to join? <b>–</b></div>
      <p>Start-up costs depend on store size and location. Our team will walk you through fees, fit-out and stock so you can plan with confidence before signing, and we help arrange finance where needed.</p></div>
    <div class="faq-item">How long does training take? <b>+</b></div>
    <div class="faq-item">Do I need floristry experience? <b>+</b></div>
    <div class="faq-item">Can you run a supermarket floral department? <b>+</b></div>
    <div class="faq-item">How soon can my store open? <b>+</b></div>
  </div>
  <div class="bouquet" role="img" aria-label="Mixed purple and pink bouquet"></div>
</section>

<section class="section contact">
  <div class="ghost">CONTACT</div>
  <form class="contact-form">
    <h2>Contact Us</h2>
    <div class="row"><div class="field">Name</div><div class="field">Email</div></div>
    <div class="row"><div class="field">Phone No</div><div class="field">Subject</div></div>
    <div class="row"><div class="field tall">Message</div></div>
    <span class="btn">Get Started <span class="dot"></span></span>
  </form>
  <div class="details">
    <h2>Contact Details</h2>
    <div class="item"><span class="ico"></span><span>120, Garden Row, Fern Park,<br>Springfield</span></div>
    <div class="item"><span class="ico"></span><span>123-456-7890</span></div>
    <div class="item"><span class="ico"></span><span>info@lanternpetals.com</span></div>
    <div class="social"><span><i></i>Facepage</span><span><i></i>Chirper</span><span><i></i>Linkwork</span></div>
  </div>
</section>

<footer class="section site-footer">
  <div class="brand"><div class="mark"></div><span>Lantern Petals</span></div>
  <nav class="flinks"><span>Home</span><span>About Us</span><span>For Supermarkets</span><span>For Franchisees</span><span>Contact Us</span></nav>
  <div class="copy">Copyright 2016 Lantern Petals. All Rights Reserved</div>
</footer>

</body>
</html>
```